Web Design

We need a website for a company based in Doha Qatar called
Lumara Maid Service.

It is the number one maid cleaning service company, and we have branches all over qatar.

Luxury Cleaning Service Provider.

The color scheme is gold, yellow and black like the logo.

Before they get to the website, there is an intro video.

The website should depict luxury.

Target Market(s)

People who need maids at their houses.

Industry/Entity Type

Cleaning Service

Requirements
Must have
• Luxury, Sleek, Modern

The opening sequence is a video which I already have. Its too big to upload here so I am going to put it on youtube.

After the opening sequence, the home page should have a widescreen photo background and it should change every five seconds, the first background photo should be of qatar westbay skyline. Then the second background should be of maid photos in cleaning positions. Then the third background should be of cleaner photos etc.

We will send you all the tabs and all the content later.

```html
<!DOCTYPE html>
<html lang="en">
<head>
<meta charset="utf-8">
<title>Lumara Maid Service</title>
<link href="https://fonts.googleapis.com/css2?family=Cabin:wght@400;500;600&family=Open+Sans:wght@400;600&family=Raleway:wght@500;600&family=Lora&display=swap" rel="stylesheet">
<style>
:root{
  --gold:#f2b51c;--gold-light:#ffd35a;--gold-deep:#e29e0a;
  --brown:#5a2a06;--ink:#3a2a1a;--text:#6b6b6b;--grey-btn:#4a4a4a;
  --panel:#e3e3e3;--footer:#2e2e2e;--footer-line:#4a4a4a;--footer-text:#cfcfcf;
  --white:#fff;
}
*{margin:0;padding:0;box-sizing:border-box}
html,body{width:731px;height:1200px;overflow:hidden;background:var(--white)}
body{position:relative;font-family:"Open Sans",sans-serif;color:var(--text)}
.abs{position:absolute}
.heading{font-family:"Cabin",sans-serif;font-weight:500;color:var(--ink);font-size:15px}
/* header */
.nav-bar{left:0;top:52px;width:731px;height:26px;background:linear-gradient(var(--gold-light),var(--gold-deep))}
.nav-bar a{position:absolute;top:0;height:26px;line-height:26px;font-size:8.5px;color:#3a2a10;text-decoration:none;transform:translateX(-50%)}
.nav-bar a.active{background:var(--brown);color:var(--white);width:63px;text-align:center;transform:none;left:329px}
.brand{left:62px;top:0;width:170px;height:92px;background:var(--white);box-shadow:0 1px 4px rgba(0,0,0,.25);display:flex;align-items:center;justify-content:center;gap:6px}
.brand-mark{width:14px;height:14px;border-radius:50%;background:var(--gold-deep)}
.brand-name{font-size:11.5px;font-weight:600;color:#9a6a1c}
.phone{left:432px;top:17px;font-size:11px;color:#555;display:flex;align-items:center;gap:5px}
.btn-top{top:17px;width:53px;height:15px;font-size:8px;text-align:center;line-height:15px}
/* hero */
.hero{left:0;top:78px;width:731px;height:318px;background:linear-gradient(180deg,#0c1230 0%,#262a5a 40%,#3a2d6a 62%,#1a2a5a 80%,#0d1533 100%)}
.slide-arrow{top:138px;width:25px;height:36px;background:var(--gold);display:flex;align-items:center;justify-content:center}
.caption{left:362px;top:99px;width:315px;height:107px;background:rgba(20,22,40,.6);text-align:center;color:var(--white)}
.caption h1{font-family:"Open Sans",sans-serif;font-weight:400;font-size:17px;margin-top:20px;letter-spacing:.3px}
.caption p{font-size:9px;line-height:13px;margin-top:5px}
.search{left:43px;top:88px;width:160px;height:16px;background:var(--white);font-size:7px;color:#888;text-align:left;padding:3px 5px}
.search-btn{left:211px;top:88px;width:68px;height:16px;background:var(--gold);font-size:8px;color:#3a2a10;line-height:16px}
/* content */
.intro{left:61px;top:443px;width:401px;font-size:8px;line-height:11px}
.service{width:130px;text-align:center}
.service .photo{width:62px;height:62px;border-radius:50%;border:3px solid #eee;box-shadow:0 0 3px rgba(0,0,0,.3);margin:0 auto}
.service h3{font-family:"Cabin",sans-serif;font-weight:600;font-size:9.5px;color:var(--ink);margin-top:11px}
.service p{font-size:8px;line-height:11px;margin-top:6px}
.btn{display:inline-block;margin-top:10px;width:54px;height:14px;line-height:14px;font-size:7.5px;color:var(--white);background:var(--grey-btn)}
.btn.gold{background:var(--gold);color:#3a2a10}
.divider{left:61px;top:689px;width:401px;height:1px;background:#ddd}
.thumb{top:739px;width:92px;height:83px}
.request{left:479px;top:592px;width:191px;height:229px;background:var(--panel)}
.request-head{height:26px;background:linear-gradient(var(--gold-light),var(--gold));font-family:"Cabin",sans-serif;font-weight:600;font-size:12px;color:var(--ink);text-align:center;line-height:26px}
.field{position:absolute;left:16px;width:160px;height:16px;background:var(--white);border:1px solid #d6d6d6;font-size:7px;color:#888;padding:3px 7px}
.select-tab{position:absolute;right:0;top:-1px;width:16px;height:16px;background:var(--gold)}
.req-btn{position:absolute;left:62px;top:203px;width:68px;height:15px;background:var(--gold);font-size:7px;font-weight:600;color:#3a2a10;text-align:center;line-height:15px}
.customer{top:889px;width:85px;height:51px;border:1px solid #ddd;display:flex;align-items:center;justify-content:center;font-size:8.5px;font-weight:600}
/* footer */
.footer{left:0;top:973px;width:731px;height:227px;background:linear-gradient(var(--footer),#3a3a3a)}
.footer .heading{color:var(--white);font-family:"Raleway",sans-serif;font-size:12px;font-weight:600;top:31px;position:absolute}
.link{position:absolute;left:60px;width:85px;font-size:7px;color:var(--white);border-bottom:1px solid var(--footer-line);padding-bottom:6px}
.avatar{position:absolute;left:172px;width:38px;height:38px;border-radius:50%;border:2px solid #ddd;background:linear-gradient(#777,#444)}
.quote{position:absolute;left:232px;width:125px;font-family:"Lora",serif;font-size:7px;line-height:11px;color:var(--footer-text)}
.quote b{display:block;font-weight:400;color:var(--gold);font-size:8px;margin-top:2px}
.quote i{font-style:normal;font-size:5.5px;font-family:"Open Sans",sans-serif}
.addr{position:absolute;left:376px;font-size:6.5px;color:var(--footer-text);line-height:10px}
.addr span{position:absolute;left:36px;color:#9a9a9a;white-space:nowrap}
.social{top:1181px;width:10px;height:10px;border-radius:50%;background:#aaa}
</style>
</head>
<body>

<header>
  <div class="abs nav-bar">
    <a class="active" href="#">Home</a>
    <a href="#" style="left:432px">About Us</a>
    <a href="#" style="left:482px">Service</a>
    <a href="#" style="left:540px">Gallery</a>
    <a href="#" style="left:592px">FAQ</a>
    <a href="#" style="left:650px">Contact Us</a>
  </div>
  <div class="abs brand"><span class="brand-mark"></span><span class="brand-name">Lumara Maid Service</span></div>
  <div class="abs phone">
    <svg width="14" height="14" viewBox="0 0 14 14"><circle cx="7" cy="7" r="6.2" fill="none" stroke="#666" stroke-width="1.2"/><path d="M4.5 4.2l1.4-.4.8 1.7-.9.7c.4.9 1 1.5 1.9 1.9l.7-.9 1.7.8-.4 1.4C7.2 9.5 4.7 7 4.5 4.2z" fill="#666"/></svg>
    0300 - 555 - 0188
  </div>
  <div class="abs btn-top" style="left:559px;background:#333;color:#fff">Register</div>
  <div class="abs btn-top" style="left:618px;background:var(--gold);color:#3a2a10">Login</div>
</header>

<section class="abs hero" role="img" aria-label="Night skyline of Doha West Bay with illuminated towers reflected in the water">
  <div class="abs slide-arrow" style="left:0"><svg width="10" height="12"><path d="M8 1L3 6l5 5" stroke="#fff" stroke-width="2.2" fill="none"/></svg></div>
  <div class="abs slide-arrow" style="left:706px"><svg width="10" height="12"><path d="M2 1l5 5-5 5" stroke="#fff" stroke-width="2.2" fill="none"/></svg></div>
  <div class="abs caption">
    <h1>LUMARA MAID SERVICE</h1>
    <p>lectus et nibh tempus consectetur.<br>congue orci eget, porttitor nunc. Nam gravida vestibulum</p>
    <div class="abs search">Search</div>
    <div class="abs search-btn">Search Now</div>
  </div>
</section>

<main>
  <h2 class="abs heading" style="left:61px;top:417px">Welcome To Lumara Maid Service</h2>
  <p class="abs intro">Nunc vel orci ante. Integer id sapien faucibus, vulputate arcu tempor, posuere metus. Donec id tristique eros. Quisque eleifend interdum neque, dapibus vulputate turpis tempor sed. purus sed, fringilla ligula. Praesent in metus at ligula pretium commodo. Integer sit amet turpis eros. Aenean non urna nibh. Quisque sit amet mi tempus, faucibus tortor eget, venenatis lorem</p>

  <div class="abs service" style="left:57px;top:515px">
    <div class="photo" role="img" aria-label="Cleaner with mop and cart in an office" style="background:linear-gradient(#c9c2b4,#8a7d6a)"></div>
    <h3>Commerical Cleaning</h3>
    <p>Nunc venenatis congue velit, eget eleifend sapien accumsan non. Sed blandit suscipit.</p>
    <span class="btn gold">Read More</span>
  </div>
  <div class="abs service" style="left:197px;top:515px">
    <div class="photo" role="img" aria-label="Maid vacuuming a living room" style="background:linear-gradient(#9fb7c7,#4f6b82)"></div>
    <h3>Residential Cleaning</h3>
    <p>Nunc venenatis congue velit, eget eleifend sapien accumsan non. Sed blandit suscipit.</p>
    <span class="btn">Read More</span>
  </div>
  <div class="abs service" style="left:335px;top:515px">
    <div class="photo" role="img" aria-label="Squeegee cleaning a window pane" style="background:radial-gradient(#a8c060,#3c5a1a)"></div>
    <h3>Window Cleaning</h3>
    <p>Nunc venenatis congue velit, eget eleifend sapien accumsan non. Sed blandit suscipit.</p>
    <span class="btn">Read More</span>
  </div>

  <div class="abs divider"></div>

  <h2 class="abs heading" style="left:61px;top:711px">Our Gallery</h2>
  <svg class="abs" style="left:442px;top:716px" width="22" height="10"><path d="M6 1L2 5l4 4" stroke="var(--gold)" stroke-width="2" fill="none"/><path d="M15 1l4 4-4 4" stroke="#222" stroke-width="2" fill="none"/></svg>
  <div class="abs thumb" style="left:62px;background:linear-gradient(#b8cde0,#e8e8e8)" role="img" aria-label="Window washer with squeegee"></div>
  <div class="abs thumb" style="left:165px;background:linear-gradient(#e6e6e6,#7a7a7a)" role="img" aria-label="Office lounge being vacuumed"></div>
  <div class="abs thumb" style="left:267px;background:linear-gradient(#3a8ab0,#5a6a78)" role="img" aria-label="Floor polishing in a bright lobby"></div>
  <div class="abs thumb" style="left:371px;background:linear-gradient(#d8d8d8,#6c6c6c)" role="img" aria-label="Cleaner tidying a waiting area"></div>

  <h2 class="abs heading" style="left:478px;top:417px">Our Video</h2>
  <div class="abs" style="left:479px;top:446px;width:191px;height:117px;border:2px solid #ddd;background:linear-gradient(90deg,#2a2a2a,#9a9a9a 55%,#555)" role="img" aria-label="Video still of a housekeeper holding folded towels">
    <svg class="abs" style="left:75px;top:44px" width="34" height="24"><rect width="34" height="24" rx="6" fill="#d21a1a"/><path d="M13 7l9 5-9 5z" fill="#fff"/></svg>
  </div>

  <form class="abs request">
    <div class="request-head">Request Service</div>
    <div class="field" style="top:41px">Your Name</div>
    <div class="field" style="top:66px">Your Email id</div>
    <div class="field" style="top:90px">State</div>
    <div class="field" style="top:116px">Request For<span class="select-tab"></span></div>
    <div class="field" style="top:141px;height:50px">Your Message</div>
    <div class="req-btn">REQUEST NOW</div>
  </form>

  <h2 class="abs heading" style="left:0;width:731px;text-align:center;top:855px">Our Customers</h2>
  <div class="abs customer" style="left:62px;color:#e8562a">Ember Co</div>
  <div class="abs customer" style="left:166px;color:#2a9ab8">Brightwell</div>
  <div class="abs customer" style="left:271px;color:#8a7a5a">Northfield</div>
  <div class="abs customer" style="left:376px;color:#c9a41a">Lumen Labs</div>
  <div class="abs customer" style="left:481px;color:#e07a10">Orbis Studio</div>
  <div class="abs customer" style="left:586px;color:#2a78c8">Signal Hub</div>
</main>

<footer class="abs footer">
  <h3 class="heading" style="left:60px">Links</h3>
  <h3 class="heading" style="left:171px">Testimonils</h3>
  <h3 class="heading" style="left:376px">Address</h3>
  <h3 class="heading" style="left:533px">Contacts</h3>

  <div class="link" style="top:66px">HOME</div>
  <div class="link" style="top:88px">FEATURES</div>
  <div class="link" style="top:109px">PAGES</div>
  <div class="link" style="top:130px">PORTFOLIO</div>
  <div class="link" style="top:152px">NEWS</div>
  <div class="link" style="top:174px;border:none">CONTACTS</div>

  <div class="avatar" style="top:57px" role="img" aria-label="Portrait of a client"></div>
  <div class="quote" style="top:68px">&nbsp;&nbsp;&nbsp;&nbsp;&nbsp;&nbsp;Pellentesque et pulvinar enim. Quisque at tempor ligula.<b>Maren Holloway</b><i>Art Director / lorem ipsum</i></div>
  <div class="avatar" style="top:124px" role="img" aria-label="Portrait of a client"></div>
  <div class="quote" style="top:136px">&nbsp;&nbsp;&nbsp;&nbsp;&nbsp;&nbsp;Pellentesque et pulvinar enim. Quisque at tempor ligula.<b>Maren Holloway</b><i>Art Director / lorem ipsum</i></div>

  <div class="addr" style="top:64px">Address:<span>24 Corniche Street Suite 310<br>&nbsp;&nbsp;Doha, Qatar</span></div>
  <div class="addr" style="top:92px">Phone:<span>+974 (555) 01 88</span></div>
  <div class="addr" style="top:108px">Email:<span>hello@lumaramaid.example</span></div>

  <div class="abs" style="left:534px;top:66px;width:136px;height:76px;background:linear-gradient(135deg,#e8e4d8,#c9d6b8 50%,#e4e0d0)" role="img" aria-label="Street map of the office location"></div>

  <div class="abs" style="left:60px;top:197px;width:610px;height:1px;background:var(--footer-line)"></div>
  <div class="abs" style="left:60px;top:208px;font-size:7px;color:#9a9a9a">lumaramaid.example © Copyright 2014, all rights reserved</div>
</footer>
<div class="abs social" style="left:586px"></div>
<div class="abs social" style="left:613px"></div>
<div class="abs social" style="left:640px"></div>
<div class="abs social" style="left:663px"></div>

</body>
</html>
```